Naturopath Practitioner Card Design

I am a naturopath needing a design for a business card mainly to show that I am a naturopath and have some contact details to give to prospective clients. I am open minded about the design and what is on the second side of the card whether it just be some artwork or space for details, appointment times etc. Naturopathy is the practice of natural medicine that uses a holistic approach and incorporates herbal and nutritional medicine.

Industry/Entity Type

Business

Contact Information for Business Card

Tom Rudd NaturopathBHSc (Naturopathy) Member WHPG 0487 925 316 tom.rudd@mailexample.com www.tomruddnaturopathy.example.au

Requirements
Nice to have
• Would prefer some kind of original pattern/art work/logo rather than an image, not fussed if its very simple/basic
• I am open to any colour but think I would prefer a more earthy sandy clay etc type style than the greens that are commonly associated with naturopathy.
Should not have
• Don't really want to have generic stock images on it

```html
<!DOCTYPE html>
<html lang="en">
<head>
<meta charset="utf-8">
<title>Tom Rudd Naturopath – Business Card</title>
<link rel="stylesheet" href="https://fonts.googleapis.com/css2?family=Arimo:wght@400;700&family=Noto+Sans:wght@400;600&display=swap">
<style>
  :root {
    --backdrop: #e9e4dc;
    --card: #ffffff;
    --ink: #111111;
    --ink-soft: #222222;
    --herb-light: #eef3e8;
    --herb-mid: #c9dbb8;
    --herb-deep: #5f8f3e;
    --pepper: #3b2c24;
  }
  * { box-sizing: border-box; margin: 0; padding: 0; }
  html, body { width: 1200px; height: 933px; overflow: hidden; }
  body { background: var(--backdrop); position: relative; font-family: "Arimo", Arial, sans-serif; color: var(--ink); }

  .card { position: absolute; left: 274px; width: 652px; height: 374px; background: var(--card); overflow: hidden; box-shadow: 0 4px 14px rgba(0,0,0,.18); }
  .card--front { top: 64px; }
  .card--back { top: 494px; font-family: "Noto Sans", Arial, sans-serif; }

  /* front */
  .herb-wash { position: absolute; left: 40px; top: 60px; width: 600px; height: 262px;
    background: radial-gradient(ellipse at 30% 55%, var(--herb-light), rgba(255,255,255,0) 70%),
                radial-gradient(ellipse at 75% 65%, #efeeee, rgba(255,255,255,0) 65%); }
  .identity { position: absolute; right: calc(652px - 334px); top: 136px; text-align: right; white-space: nowrap; }
  .identity__name { font-size: 29px; font-weight: 700; letter-spacing: .5px; line-height: 1; }
  .identity__role { font-size: 19px; margin-top: 10px; line-height: 1; color: var(--ink-soft); }
  .identity__creds { font-size: 17px; margin-top: 10px; line-height: 1; color: var(--ink-soft); }
  .divider { position: absolute; left: 358px; top: 68px; width: 2px; height: 226px; background: var(--ink); }
  .contacts { position: absolute; left: 382px; top: 154px; list-style: none; }
  .contacts li { display: flex; align-items: center; gap: 10px; font-size: 17px; height: 20px; margin-bottom: 10px; white-space: nowrap; }
  .contacts svg { width: 17px; height: 17px; flex: none; }
  .rule-thin { position: absolute; left: 0; right: 0; top: 321px; height: 3px; background: var(--ink); }
  .band { position: absolute; left: 0; right: 0; top: 327px; bottom: 0; background: var(--ink); }

  /* back */
  .appt__title { position: absolute; left: 0; right: 0; top: 38px; text-align: center; font-size: 27px; font-weight: 600; }
  .appt__rule { position: absolute; left: 50px; width: 557px; top: 87px; height: 2px; background: var(--ink); }
  .label { position: absolute; font-size: 19px; font-weight: 600; line-height: 1; }
  .label--small { font-size: 17px; }
  .dots { position: absolute; height: 0; border-top: 2px dotted var(--ink); }
  .herb-still { position: absolute; left: 136px; top: 186px; width: 370px; height: 164px;
    background: radial-gradient(ellipse at 30% 55%, var(--herb-deep) 0%, var(--herb-mid) 45%, rgba(255,255,255,0) 72%),
                radial-gradient(ellipse at 78% 70%, var(--pepper) 0%, #cfc7c0 35%, rgba(255,255,255,0) 60%); }
</style>
</head>
<body>
  <section class="card card--front" aria-label="Business card front">
    <div class="herb-wash" role="img" aria-label="Faded photo of fresh herbs, mortar and pestle and a bowl of peppercorns"></div>
    <div class="identity">
      <p class="identity__name">Tom Rudd</p>
      <p class="identity__role">Naturopath</p>
      <p class="identity__creds">BHSc (Naturopathy) Member WHPG</p>
    </div>
    <div class="divider"></div>
    <ul class="contacts">
      <li>
        <svg viewBox="0 0 20 20" aria-hidden="true"><rect width="20" height="20" fill="#111"/><path d="M6 4c1 0 2 2.5 2 3s-1 1-1 1.5 2 3.5 3.5 3.8c.5 0 1-1 1.5-1s3 1 3 2-1.5 2.2-2.5 2.2C8 15.5 4.5 11 4.5 6.5 4.5 5 5 4 6 4z" fill="#fff"/></svg>
        <span>0487 925 316</span>
      </li>
      <li>
        <svg viewBox="0 0 20 20" aria-hidden="true"><rect width="20" height="20" fill="#111"/><rect x="3" y="5" width="14" height="10" fill="none" stroke="#fff" stroke-width="1.5"/><path d="M3 5l7 6 7-6" fill="none" stroke="#fff" stroke-width="1.5"/></svg>
        <span>tom.rudd@mailexample.com</span>
      </li>
    </ul>
    <div class="rule-thin"></div>
    <div class="band"></div>
  </section>

  <section class="card card--back" aria-label="Business card back, appointment">
    <h2 class="appt__title">Appointment</h2>
    <div class="appt__rule"></div>
    <span class="label" style="left:48px; top:117px;">Date</span>
    <div class="dots" style="left:101px; width:225px; top:131px;"></div>
    <span class="label" style="left:334px; top:113px;">At</span>
    <div class="dots" style="left:366px; width:204px; top:131px;"></div>
    <span class="label label--small" style="right:45px; top:106px;">am.</span>
    <span class="label label--small" style="right:45px; top:130px;">pm.</span>
    <div class="dots" style="left:50px; width:557px; top:150px;"></div>
    <div class="dots" style="left:50px; width:557px; top:175px;"></div>
    <div class="dots" style="left:50px; width:557px; top:198px;"></div>
    <div class="herb-still" role="img" aria-label="Photo of fresh basil, thyme and rosemary with a white mortar, a dish of salt and a bowl of black peppercorns"></div>
  </section>
</body>
</html>
```